Law Offices business card

Hi there, I'll need business card for the Law Offices of Colin Matheny. The information must convey his strategic approach and quick resolution to complex business litigation needs. Please emphasize Civil Litigation, Corporate Law, Business Governance and Real Estate Law. Colin has over 25 years of experience in these fields.The card should be modern and edgy and the message should be clear. Please consult his current website for ideas.

```html
<!DOCTYPE html>
<html lang="en">
<head>
<meta charset="utf-8">
<title>Law Offices of Colin Matheny – Business Card</title>
<link rel="stylesheet" href="https://fonts.googleapis.com/css2?family=Libre+Baskerville:wght@400;700&family=Arimo:wght@400&display=swap">
<style>
  :root {
    --gold: #b6962c;
    --gold-deep: #a3841f;
    --ink: #111111;
    --paper: #ffffff;
    --text-grey: #2b2b2b;
    --backdrop: #e9e6e0;
  }
  * { margin: 0; padding: 0; box-sizing: border-box; }
  html, body {
    width: 1200px;
    height: 892px;
    overflow: hidden;
    background: var(--backdrop);
  }
  .canvas {
    position: relative;
    width: 1200px;
    height: 892px;
  }
  .card {
    position: absolute;
    width: 560px;
    height: 320px;
    background: var(--gold);
    box-shadow: 0 6px 18px rgba(0,0,0,0.18);
    overflow: hidden;
  }
  .card-front { left: 70px; top: 110px; }
  .card-back { left: 570px; top: 462px; }
  .card-shape {
    position: absolute;
    inset: 0;
    width: 100%;
    height: 100%;
  }
  .front-content {
    position: absolute;
    left: 38px;
    top: 34px;
  }
  .holder-name {
    font-family: "Libre Baskerville", serif;
    font-size: 33px;
    color: var(--gold);
    line-height: 1.1;
  }
  .holder-title {
    font-family: "Libre Baskerville", serif;
    font-size: 19px;
    color: var(--ink);
    margin-top: 2px;
  }
  .firm-name {
    font-family: "Libre Baskerville", serif;
    font-weight: 700;
    font-size: 19px;
    color: var(--ink);
    margin-top: 14px;
  }
  .contact-list {
    list-style: none;
    margin-top: 20px;
  }
  .contact-item {
    display: flex;
    align-items: center;
    gap: 12px;
    font-family: "Arimo", sans-serif;
    font-size: 14px;
    color: var(--text-grey);
    height: 23px;
  }
  .contact-icon {
    width: 15px;
    height: 15px;
    flex: none;
  }
  .practice-areas {
    position: absolute;
    right: 40px;
    bottom: 30px;
    text-align: center;
    font-family: "Arimo", sans-serif;
    color: var(--ink);
  }
  .practice-area {
    font-size: 19px;
    line-height: 1.75;
  }
</style>
</head>
<body>
<div class="canvas">

  <section class="card card-front" aria-label="Business card front">
    <svg class="card-shape" viewBox="0 0 560 320" aria-hidden="true">
      <path d="M0 0 H410 C500 90 500 230 440 320 H0 Z" fill="var(--ink)"/>
      <path d="M0 0 H392 C476 90 476 230 418 320 H0 Z" fill="var(--paper)"/>
    </svg>
    <div class="front-content">
      <div class="holder-name">Colin Matheny</div>
      <div class="holder-title">Attorney</div>
      <div class="firm-name">Law Offices of Colin Matheny, P.A.</div>
      <ul class="contact-list">
        <li class="contact-item">
          <svg class="contact-icon" viewBox="0 0 15 15" aria-hidden="true"><rect width="15" height="15" fill="var(--gold)"/><path d="M4 3.5h2l.8 2.2-1.2.8a5 5 0 0 0 2.9 2.9l.8-1.2 2.2.8v2A1 1 0 0 1 10.5 12 7.5 7.5 0 0 1 3 4.5 1 1 0 0 1 4 3.5z" fill="#fff"/></svg>
          561-555-0142
        </li>
        <li class="contact-item">
          <svg class="contact-icon" viewBox="0 0 15 15" aria-hidden="true"><rect width="15" height="15" fill="var(--gold)"/><rect x="4.5" y="2.5" width="6" height="10" rx="1" fill="#fff"/><rect x="5.5" y="4" width="4" height="6" fill="var(--gold)"/></svg>
          561-555-0178
        </li>
        <li class="contact-item">
          <svg class="contact-icon" viewBox="0 0 15 15" aria-hidden="true"><rect width="15" height="15" fill="var(--gold)"/><rect x="3" y="4.5" width="9" height="6" fill="#fff"/><path d="M3 4.5l4.5 3.5 4.5-3.5" stroke="var(--gold)" fill="none"/></svg>
          colin@mathenylaw.com
        </li>
        <li class="contact-item">
          <svg class="contact-icon" viewBox="0 0 15 15" aria-hidden="true"><rect width="15" height="15" fill="var(--gold)"/><circle cx="7.5" cy="7.5" r="4.5" fill="none" stroke="#fff"/><ellipse cx="7.5" cy="7.5" rx="2" ry="4.5" fill="none" stroke="#fff"/><path d="M3 7.5h9" stroke="#fff"/></svg>
          www.mathenylaw.com
        </li>
        <li class="contact-item">
          <svg class="contact-icon" viewBox="0 0 15 15" aria-hidden="true"><rect width="15" height="15" fill="var(--gold)"/><path d="M7.5 2.5a3.5 3.5 0 0 1 3.5 3.5c0 2.5-3.5 6.5-3.5 6.5S4 8.5 4 6a3.5 3.5 0 0 1 3.5-3.5z" fill="#fff"/><circle cx="7.5" cy="6" r="1.2" fill="var(--gold)"/></svg>
          118B Harbor Lane, Palm Beach, Florida 33480
        </li>
      </ul>
    </div>
  </section>

  <section class="card card-back" aria-label="Business card back">
    <svg class="card-shape" viewBox="0 0 560 320" aria-hidden="true">
      <path d="M0 320 V238 C70 110 260 28 560 14 V320 Z" fill="var(--ink)"/>
      <path d="M0 320 V262 C78 128 268 48 560 34 V320 Z" fill="var(--paper)"/>
    </svg>
    <div class="practice-areas">
      <div class="practice-area">Civil Litigation</div>
      <div class="practice-area">Corporate Law</div>
      <div class="practice-area">Business Governance and Real Estate Law</div>
    </div>
  </section>

</div>
</body>
</html>
```